Looking for a cool & simple business-card-design for digital agency

Hi!

We are a web agency that offers Reputation Management, Vextor & Seo Services and software development. We like cool things, we like innovative styles.

We have uploaded our logo.

Project Deadline Extended Reason: Client does not want any designs with the colorful logo. Please send us submissions ONLY with the blac and white logo. What the client would like to see:1) Back of the card: is a silver logo on a black background2) front of the card with all the data, please use white background and black logo thank you Added Friday, May 8, 2015

Industry/Entity Type

Software

```html
<!DOCTYPE html>
<html lang="de">
<head>
<meta charset="utf-8">
<title>Lumaris AG – Visitenkarte</title>
<link href="https://fonts.googleapis.com/css2?family=Lato:wght@400;700&display=swap" rel="stylesheet">
<style>
  :root {
    --stage: #2f2f31;
    --card-black: #060606;
    --card-white: #ffffff;
    --ink: #111111;
    --silver: #c9c9cc;
    --silver-dim: #9a9a9e;
  }
  * { box-sizing: border-box; margin: 0; padding: 0; }
  html, body {
    width: 1200px; height: 795px; overflow: hidden;
    background: var(--stage);
    font-family: "Lato", Arial, sans-serif;
  }
  .canvas { position: relative; width: 1200px; height: 795px; }
  .card {
    position: absolute; top: 250px;
    width: 520px; height: 297px;
    overflow: hidden;
  }
  .card--back { left: 50px; background: var(--card-black); }
  .card--front { left: 630px; background: var(--card-white); color: var(--ink); }

  .brand { display: flex; align-items: center; gap: 12px; }
  .brand__mark { width: 18px; height: 18px; flex: none; }
  .brand__name { font-weight: 700; letter-spacing: 1px; line-height: 1; }
  .brand__tagline {
    font-weight: 400; text-transform: uppercase; line-height: 1;
  }

  .card--back .brand-block {
    position: absolute; left: 70px; top: 110px;
  }
  .card--back .brand__mark { background: var(--silver); width: 30px; height: 30px; }
  .card--back .brand__name { color: var(--silver); font-size: 42px; }
  .card--back .brand__tagline {
    color: var(--silver-dim); font-size: 17px; letter-spacing: 7px;
    margin: 10px 0 0 42px;
  }

  .card--front .brand-block { position: absolute; left: 30px; top: 26px; }
  .card--front .brand__mark { background: var(--ink); width: 14px; height: 14px; }
  .card--front .brand__name { font-size: 22px; }
  .card--front .brand__tagline {
    font-size: 9px; letter-spacing: 3.5px; margin: 4px 0 0 26px; color: #333;
  }

  .person { position: absolute; left: 30px; top: 88px; }
  .person__name { font-weight: 700; font-size: 16px; }
  .person__role { font-size: 13px; margin-top: 2px; }

  .contacts { position: absolute; left: 30px; top: 146px; list-style: none; }
  .contacts li {
    display: flex; align-items: center; gap: 6px;
    font-size: 15px; line-height: 19px;
  }
  .contacts svg { width: 12px; height: 12px; flex: none; fill: var(--ink); }

  .card__band {
    position: absolute; left: 0; right: 0; bottom: 0; height: 58px;
    background: var(--card-black);
  }
  .card__corner {
    position: absolute; right: 40px; bottom: 30px;
    width: 110px; height: 110px; background: var(--card-black);
  }
</style>
</head>
<body>
<main class="canvas">

  <section class="card card--back" aria-label="Rückseite">
    <div class="brand-block">
      <div class="brand">
        <span class="brand__mark"></span>
        <span class="brand__name">Lumaris AG</span>
      </div>
      <p class="brand__tagline">Digitale Strategien</p>
    </div>
  </section>

  <section class="card card--front" aria-label="Vorderseite">
    <div class="brand-block">
      <div class="brand">
        <span class="brand__mark"></span>
        <span class="brand__name">Lumaris AG</span>
      </div>
      <p class="brand__tagline">Digitale Strategien</p>
    </div>

    <div class="person">
      <p class="person__name">Daria Keller</p>
      <p class="person__role">Director</p>
    </div>

    <ul class="contacts">
      <li>
        <svg viewBox="0 0 24 24" aria-hidden="true"><path d="M3 8c0-3 4-5 9-5s9 2 9 5v2h-5V8H8v2H3zM6 12h12l2 9H4z"/></svg>
        000 555 8812
      </li>
      <li>
        <svg viewBox="0 0 24 24" aria-hidden="true"><path d="M7 1h10a2 2 0 0 1 2 2v18a2 2 0 0 1-2 2H7a2 2 0 0 1-2-2V3a2 2 0 0 1 2-2zm0 3v14h10V4z"/></svg>
        333 7720 419
      </li>
      <li>
        <svg viewBox="0 0 24 24" aria-hidden="true"><path d="M2 5h20v14H2zm2 2v1l8 5 8-5V7l-8 5z"/></svg>
        info@lumarisag.com
      </li>
      <li>
        <svg viewBox="0 0 24 24" aria-hidden="true"><path d="M12 2a10 10 0 1 0 0 20 10 10 0 0 0 0-20zm-1 2.1V8H7.4A8 8 0 0 1 11 4.1zm2 0A8 8 0 0 1 16.6 8H13zM4.5 10H11v4H4.5a8 8 0 0 1 0-4zM13 10h6.5a8 8 0 0 1 0 4H13zm-5.6 6H11v3.9A8 8 0 0 1 7.4 16zm5.6 0h3.6a8 8 0 0 1-3.6 3.9z"/></svg>
        www.lumarisag.com
      </li>
    </ul>

    <div class="card__band"></div>
    <div class="card__corner"></div>
  </section>

</main>
</body>
</html>
```